Kesso Tea Premium Matcha brand Label

This is a label design project for a luxury tea brand. Feel free to be creative within the guidelines.
Attached to this project is a document called “Private Label Design Requirements” with the design guidelines and template. There is another document called "Kesso Tea Packaging Instructions" this has more details necessary to stick to the guidelines in the first document.

I have also attached the certifications to be included as well as different variations of the logo for you to use.

If you have any questions, I am here.
Updates

Need extra days to review

Target Market(s)

Young, active, fun, enjoy the finer things

```html
<!DOCTYPE html>
<html lang="en">
<head>
<meta charset="utf-8">
<title>Kesso Tea – Premium Organic Ceremonial Matcha Labels</title>
<link rel="stylesheet" href="https://fonts.googleapis.com/css2?family=Bebas+Neue&family=Barlow+Condensed:wght@600&family=Barlow:wght@500;600&display=swap">
<style>
  :root {
    --page-bg: #ececee;
    --label-dark: #14532b;
    --label-edge: #0f4423;
    --netwt-green: #1f8a43;
    --logo-panel: #b8e0a6;
    --banner-green: #72c64f;
    --banner-bright: #8edc6c;
    --banner-ink: #1a5a2b;
    --white: #ffffff;
    --mark-dark: #1d1d1d;
    --mark-light: #a8e88a;
  }
  * { margin: 0; padding: 0; box-sizing: border-box; }
  html, body {
    width: 1200px; height: 723px; overflow: hidden;
    background: var(--page-bg);
  }
  .canvas {
    position: relative; width: 1200px; height: 723px;
  }
  .label {
    position: absolute; top: 206px;
    width: 520px; height: 310px;
    overflow: hidden;
  }
  .label--classic { left: 60px; }
  .label--modern { left: 620px; }
  .label__ground {
    position: absolute; inset: 0;
    background: linear-gradient(90deg, var(--label-edge) 0%, var(--label-dark) 12%, var(--label-dark) 88%, var(--label-edge) 100%);
  }

  /* Classic variant */
  .brand-panel {
    position: absolute; left: 0; top: 0; width: 164px; height: 162px;
    background: var(--logo-panel);
    display: flex; flex-direction: column; align-items: center; justify-content: center; gap: 12px;
  }
  .brand-panel__dot {
    width: 52px; height: 52px; border-radius: 50%;
    background: var(--label-dark);
  }
  .brand-panel__name {
    font-family: "Barlow Condensed", sans-serif; font-weight: 600;
    font-size: 20px; color: var(--mark-dark); letter-spacing: 0.5px;
  }
  .product-name {
    position: absolute;
    font-family: "Bebas Neue", sans-serif;
    color: var(--white); line-height: 1; white-space: nowrap;
  }
  .label--classic .product-name { left: 188px; top: 68px; font-size: 86px; }
  .net-weight {
    position: absolute; width: 164px; height: 81px;
    background: var(--netwt-green); color: var(--white);
    font-family: "Barlow", sans-serif;
    display: flex; flex-direction: column; align-items: center; justify-content: center;
  }
  .label--classic .net-weight { left: 0; top: 162px; }
  .net-weight__caption { font-size: 17px; font-weight: 500; line-height: 1.1; }
  .net-weight__value { font-size: 38px; font-weight: 600; line-height: 1; }
  .net-weight__imperial {
    position: absolute; width: 164px; text-align: center;
    font-family: "Barlow", sans-serif; font-weight: 500;
    font-size: 17px; color: var(--white);
  }
  .label--classic .net-weight__imperial { left: 0; top: 249px; }
  .tagline {
    position: absolute; height: 81px;
    display: flex; flex-direction: column; justify-content: center;
    padding-left: 24px;
    font-family: "Barlow Condensed", sans-serif; font-weight: 600;
    font-size: 29px; line-height: 1.08; letter-spacing: 1.2px;
  }
  .label--classic .tagline {
    left: 164px; top: 162px; width: 307px;
    background: var(--banner-green); color: var(--banner-ink);
  }

  /* Modern variant */
  .label--modern .brand-dot {
    position: absolute; left: 26px; top: 80px;
    width: 120px; height: 120px; border-radius: 50%;
    background: var(--mark-light); opacity: 0.85;
  }
  .label--modern .product-name { left: 168px; top: 78px; font-size: 82px; }
  .label--modern .net-weight {
    left: 24px; top: 165px; height: 80px; width: 142px;
    background: var(--netwt-green);
  }
  .label--modern .net-weight__imperial { left: 24px; top: 252px; width: 142px; }
  .label--modern .tagline {
    left: 166px; top: 165px; width: 314px; height: 80px;
    background: linear-gradient(90deg, var(--banner-green), var(--banner-bright));
    color: var(--white);
  }
</style>
</head>
<body>
<main class="canvas">

  <section class="label label--classic" aria-label="Kesso Tea label, classic layout">
    <div class="label__ground" role="img" aria-label="Dark green background with faint tea leaf pattern"></div>
    <div class="brand-panel">
      <span class="brand-panel__dot"></span>
      <span class="brand-panel__name">Kesso Tea</span>
    </div>
    <h1 class="product-name">KESSO TEA</h1>
    <div class="net-weight">
      <span class="net-weight__caption">Net Wt:</span>
      <span class="net-weight__value">30g</span>
    </div>
    <p class="net-weight__imperial">1.06oz</p>
    <p class="tagline"><span>PREMIUM ORGANIC</span><span>CEREMONIAL MATCHA</span></p>
  </section>

  <section class="label label--modern" aria-label="Kesso Tea label, modern layout">
    <div class="label__ground" role="img" aria-label="Dark green background with faint tea leaf pattern"></div>
    <span class="brand-dot"></span>
    <h1 class="product-name">KESSO TEA</h1>
    <div class="net-weight">
      <span class="net-weight__caption">Net Wt:</span>
      <span class="net-weight__value">30g</span>
    </div>
    <p class="net-weight__imperial">1.06oz</p>
    <p class="tagline"><span>PREMIUM ORGANIC</span><span>CEREMONIAL MATCHA</span></p>
  </section>

</main>
</body>
</html>
```